Satchel & Sundial needs new business card design

I need a new business card design. I'm looking for out-of-the-box design which represents the freedom of being a location independent entrepreneur.
I offer coaching, retreats and trips.
I would like to see designs with and without the photo.
Colors I use are black (#000000), green (#25A796) and brown (#D7C38C)
Website satchelandsundial.example

Target Market(s)

location independent entrepreneurs, digital nomads, people looking to swap the 9 to 5 for a lifestyle business

Industry/Entity Type

Business

Contact Information for Business Card

Dorota Falkner
Your Lifestyle Business Coach, Retreat & Trip Leader
http://satchelandsundial.example
hello@satchelandsundial.example
Live a life you don't need a holiday from

Font styles to use
Serif
Sans Serif

Requirements
Must have
• One side should contain only the logo. I would also consider having the "Live a life you don't need a holiday from" on that side too (depending on how it looks)
• Please show both sides on the designs.

```html
<!DOCTYPE html>
<html lang="en">
<head>
<meta charset="utf-8">
<title>Satchel &amp; Sundial – Business Card</title>
<link rel="stylesheet" href="https://fonts.googleapis.com/css2?family=Oswald:wght@300;400;500&family=Roboto:wght@400&display=swap">
<style>
  :root {
    --ink: #111111;
    --black: #1b1b1b;
    --green: #25a796;
    --green-deep: #0f8a7a;
    --gold: #d7c38c;
    --gold-card: #cfbd86;
    --paper: #fbfbfb;
    --backdrop: #e7e7e7;
    --white: #ffffff;
  }
  * { margin: 0; padding: 0; box-sizing: border-box; }
  html, body { width: 1200px; height: 576px; overflow: hidden; }
  body {
    background: var(--backdrop);
    position: relative;
    font-family: "Oswald", sans-serif;
  }
  .card {
    position: absolute;
    top: 138px;
    width: 484px;
    height: 294px;
    border-radius: 8px;
    overflow: hidden;
  }
  .card--front {
    left: 82px;
    background: linear-gradient(180deg, #d3c28d 0%, var(--gold-card) 100%);
    display: flex;
    align-items: center;
    justify-content: center;
  }
  .card--back { left: 602px; background: var(--paper); }

  .wordmark {
    font-family: "Oswald", sans-serif;
    font-weight: 400;
    color: var(--ink);
    text-transform: uppercase;
    letter-spacing: 1px;
    white-space: nowrap;
  }
  .card--front .wordmark { font-size: 38px; margin-top: -8px; }
  .card--back .wordmark {
    position: absolute;
    left: 30px;
    top: 122px;
    font-size: 21px;
  }

  .divider {
    position: absolute;
    left: 236px;
    top: 58px;
    width: 1px;
    height: 148px;
    background: var(--gold);
  }

  .contact { position: absolute; left: 272px; top: 68px; }
  .contact__name {
    font-weight: 500;
    font-size: 20px;
    line-height: 24px;
    color: var(--ink);
    text-transform: uppercase;
    letter-spacing: 0.3px;
  }
  .contact__role {
    margin-top: 3px;
    font-weight: 400;
    font-size: 11.5px;
    line-height: 14.5px;
    color: var(--green-deep);
  }
  .contact__list { list-style: none; margin-top: 9px; }
  .contact__item {
    display: flex;
    align-items: center;
    height: 21px;
    font-weight: 400;
    font-size: 12.5px;
    color: var(--ink);
  }
  .contact__icon { width: 11px; height: 11px; margin-right: 8px; flex: none; }
  .contact__item--social { color: var(--green-deep); }
  .contact__dot {
    width: 9px; height: 9px; margin-right: 10px;
    background: var(--black); border-radius: 2px; flex: none;
  }

  .footer-band { position: absolute; left: 0; bottom: 0; width: 484px; height: 38px; }
  .tagline {
    position: absolute;
    right: 22px;
    bottom: 10px;
    font-family: "Roboto", sans-serif;
    font-size: 13px;
    color: var(--white);
    white-space: nowrap;
  }
</style>
</head>
<body>

  <section class="card card--front" aria-label="Card front">
    <p class="wordmark">Satchel &amp; Sundial</p>
  </section>

  <section class="card card--back" aria-label="Card back">
    <p class="wordmark">Satchel &amp; Sundial</p>
    <div class="divider"></div>

    <div class="contact">
      <h1 class="contact__name">Dorota Falkner</h1>
      <p class="contact__role">Your Lifestyle Business Coach<br>Retreat &amp; Trip Leader</p>
      <ul class="contact__list">
        <li class="contact__item">
          <svg class="contact__icon" viewBox="0 0 12 12" aria-hidden="true">
            <rect x="0.5" y="2" width="11" height="8" fill="var(--green-deep)"/>
            <polyline points="0.5,2 6,6.5 11.5,2" fill="none" stroke="var(--white)" stroke-width="1"/>
          </svg>
          hello@satchelandsundial.example
        </li>
        <li class="contact__item">
          <svg class="contact__icon" viewBox="0 0 12 12" aria-hidden="true" fill="none" stroke="var(--green-deep)" stroke-width="1">
            <circle cx="6" cy="6" r="5.2"/>
            <ellipse cx="6" cy="6" rx="2.3" ry="5.2"/>
            <line x1="0.8" y1="6" x2="11.2" y2="6"/>
          </svg>
          www.satchelandsundial.example
        </li>
        <li class="contact__item contact__item--social">
          <span class="contact__dot" aria-hidden="true"></span>
          /satchelandsundial
        </li>
      </ul>
    </div>

    <svg class="footer-band" viewBox="0 0 484 38" aria-hidden="true">
      <rect x="0" y="19" width="484" height="19" fill="var(--green-deep)"/>
      <polygon points="216,0 484,0 484,38 190,38" fill="var(--black)"/>
    </svg>
    <p class="tagline">Live a life you don't need a holiday from</p>
  </section>

</body>
</html>
```